New Business Card Design for Houston-based Office Building Association

We need a business card design for our membership association in Houston known at Houston PELQ (Houston Tower Keepers & Stewards Guild). Our members are office building managers and vendors in the commercial real estate industry. Any building imagery should be of office buildings, skyscrapers, skylines, etc. (Please do NOT use houses or residential homes.) The final design should be clean and cohesive utilizing our logo and branding. I've attached our logos, branding guide, and the information to be included on the business cards.

Target Market(s)

Professionals in office buildings and commercial real estate. Our market is conservative, modern and upmarket.

Contact Information for Business Card

Should include: name, title, email, direct phone number, cell phone number, address, and possibly website. Our address is 4 Larkmoor Court, Suite 300, Houston TX 77021. Our website is houstonpelq.org. Other fields should be editable for each employee.

Colors
ffffff
33b8a4
86cfc6
00a990

Requirements
Must have
• Clean, professional, modern, look, integrating our branding, logo and colors. Our logo font is Gotham Light and signature color is PMS color Pantone 2401C (hex code 40a89d.) Our accent color is PMS color Pantone Cool Gray 10C (hex code: 636466)
Should not have
• NO imagery of homes or residential houses. We represent commercial real estate/office buildings only.

```html
<!DOCTYPE html>
<html lang="en">
<head>
<meta charset="utf-8">
<title>Houston PELQ – Business Card</title>
<link href="https://fonts.googleapis.com/css2?family=Montserrat:wght@400&display=swap" rel="stylesheet">
<style>
  :root {
    --brand-teal: #3da99d;
    --accent-gray: #636466;
    --paper: #ffffff;
    --backdrop: #2b2b2b;
  }
  * { margin: 0; padding: 0; box-sizing: border-box; }
  html, body {
    width: 1189px; height: 1200px; overflow: hidden;
    background: var(--backdrop);
    font-family: "Montserrat", Arial, sans-serif;
  }
  .card {
    position: absolute; left: 171px; width: 856px; height: 490px;
  }
  .card-front { top: 66px; background: var(--brand-teal); color: var(--paper); }
  .card-back { top: 625px; background: var(--paper); }

  /* front */
  .front-brand {
    position: absolute; left: 0; right: 0; top: 184px; height: 124px;
    display: flex; align-items: center; justify-content: center; gap: 30px;
  }
  .front-dot {
    width: 124px; height: 124px; border-radius: 50%; background: var(--paper); flex: none;
  }
  .front-name {
    font-weight: 400; font-size: 44px; letter-spacing: 0.5px; white-space: nowrap;
  }
  .front-url {
    position: absolute; left: 0; right: 0; top: 390px; text-align: center;
    font-weight: 400; font-size: 21px; letter-spacing: 6px;
  }

  /* back */
  .back-dot {
    position: absolute; left: 151px; top: 158px; width: 120px; height: 120px;
    border-radius: 50%; background: var(--brand-teal);
  }
  .back-name {
    position: absolute; left: 0; width: 422px; top: 302px; text-align: center;
    font-weight: 400; font-size: 34px; color: var(--accent-gray); white-space: nowrap;
  }
  .back-divider {
    position: absolute; left: 422px; top: 150px; width: 1px; height: 194px;
    background: var(--brand-teal);
  }
  .person-name {
    position: absolute; left: 476px; top: 143px;
    font-weight: 400; font-size: 27px; color: var(--accent-gray); letter-spacing: 1px;
  }
  .person-title {
    position: absolute; left: 476px; top: 175px;
    font-weight: 400; font-size: 20px; color: var(--brand-teal); letter-spacing: 1px;
  }
  .contact-list { position: absolute; left: 474px; top: 230px; list-style: none; }
  .contact-item {
    display: flex; align-items: center; height: 29.5px;
    font-weight: 400; font-size: 21px; color: var(--accent-gray); letter-spacing: 0.5px;
  }
  .contact-icon { width: 27px; height: 27px; margin-right: 12px; flex: none; }
  .address-band {
    position: absolute; left: 0; top: 428px; width: 780px; height: 38px;
    background: var(--brand-teal); color: var(--paper);
    font-weight: 400; font-size: 21px; line-height: 38px; padding-left: 59px; letter-spacing: 0.5px;
  }
  .band-dot {
    position: absolute; left: 753px; top: 425px; width: 44px; height: 44px;
    border-radius: 50%; background: var(--brand-teal); border: 2px solid var(--paper);
  }
</style>
</head>
<body>
  <section class="card card-front">
    <div class="front-brand">
      <div class="front-dot"></div>
      <div class="front-name">Houston PELQ</div>
    </div>
    <div class="front-url">houstonpelq.org</div>
  </section>

  <section class="card card-back">
    <div class="back-dot"></div>
    <div class="back-name">Houston PELQ</div>
    <div class="back-divider"></div>
    <div class="person-name">DANA WHITFIELD</div>
    <div class="person-title">Owner</div>
    <ul class="contact-list">
      <li class="contact-item">
        <svg class="contact-icon" viewBox="0 0 28 28" aria-hidden="true"><circle cx="14" cy="14" r="14" fill="#3da99d"/><rect x="10" y="7" width="8" height="14" rx="1.5" fill="none" stroke="#fff" stroke-width="1.8"/><circle cx="14" cy="18.5" r="0.9" fill="#fff"/></svg>
        (713) 555-0148
      </li>
      <li class="contact-item">
        <svg class="contact-icon" viewBox="0 0 28 28" aria-hidden="true"><circle cx="14" cy="14" r="14" fill="#3da99d"/><path d="M7 12c0-3 14-3 14 0v1.5h-3.5v-1.5h-7v1.5H7z" fill="#fff"/><rect x="9" y="14" width="10" height="6" rx="1" fill="#fff"/></svg>
        (713) 555-0148
      </li>
      <li class="contact-item">
        <svg class="contact-icon" viewBox="0 0 28 28" aria-hidden="true"><circle cx="14" cy="14" r="14" fill="#3da99d"/><rect x="7.5" y="9" width="13" height="10" fill="none" stroke="#fff" stroke-width="1.6"/><path d="M7.5 9l6.5 5.5 6.5-5.5" fill="none" stroke="#fff" stroke-width="1.6"/></svg>
        info@houstonpelq.org
      </li>
      <li class="contact-item">
        <svg class="contact-icon" viewBox="0 0 28 28" aria-hidden="true"><circle cx="14" cy="14" r="14" fill="#3da99d"/><g fill="none" stroke="#fff" stroke-width="1.4"><circle cx="14" cy="14" r="7"/><ellipse cx="14" cy="14" rx="3" ry="7"/><path d="M7 14h14M8.5 10.5h11M8.5 17.5h11"/></g></svg>
        houstonpelq.org
      </li>
    </ul>
    <div class="address-band">4 Larkmoor Court, Suite 300, Houston TX 77021</div>
    <div class="band-dot"></div>
  </section>
</body>
</html>
```